Ledger Lanternfox Powerpoint with Marshal Valorline Type Theme

Need powerpoint template with matching colors and different slide options. Logo and colors to be used can be found at ledgerlanternfox.example. Want brightly colored slide deck that is readable form the back of a room, but highlights colors. I will be incorporating Quizzap into the slides to gamify my presentations.

Target Market(s)

Tech

Industry/Entity Type

IT, specifically database, but crossing over to mental health in IT, important note this is not for a company, this is just for a professional building a brand

Font styles to use
Sans Serif

Colors
0054AA
0677BA
7BADD7
CADEEF
E8F1F8
EB3D1F
EC4F4E
F09395
F8D3D4
FCEDEE

Requirements
Must have
• My Logo in the bottom corner, front page, a thank your page, question page, content page, content page with two columns, content page with graphs, and icons to be used in the primary colors of the logos, About Me Page, Break Slides, Demo break slide
Should not have
• Lighter shades of colors, I want to pop out where colors are used, I want spacing and font size to be readable from the back of a room, most likely black text and white background

```html
<!DOCTYPE html>
<html lang="en">
<head>
<meta charset="utf-8">
<title>Ledger Lanternfox – Slide Deck Theme</title>
<link href="https://fonts.googleapis.com/css2?family=Questrial&display=swap" rel="stylesheet">
<style>
  :root{
    --navy:#0b3f8c;
    --blue:#0677BA;
    --sky:#13a0df;
    --red:#e0322f;
    --red-soft:#ec4f4e;
    --ink:#1f3a78;
    --grey:#4f5660;
    --light:#b9bec6;
    --white:#ffffff;
  }
  *{box-sizing:border-box;margin:0;padding:0}
  html,body{width:1143px;height:1200px;overflow:hidden;background:#fff}
  body{position:relative;font-family:"Questrial",sans-serif;color:var(--ink)}
  .slide{position:absolute;width:280px;height:158px;overflow:hidden;background:var(--white);box-shadow:0 2px 7px rgba(0,0,0,.28)}
  .abs{position:absolute}
  .photo{position:absolute}
  .title{font-size:13px;line-height:1.12;color:var(--ink)}
  .sub{font-size:3.6px;color:var(--grey);margin-top:3px}
  .para{font-size:3px;line-height:1.7;color:var(--grey)}
  .para.sm{font-size:2.6px;line-height:1.65}
  .head{font-size:3.8px;line-height:1.3;color:var(--ink)}
  .white{color:var(--white)}
  .white .sub,.white .para,.sub.white,.para.white{color:rgba(255,255,255,.93)}
  .head.white{color:#fff}
  .foot{position:absolute;left:18px;bottom:5px;font-size:4px;color:var(--navy);display:flex;align-items:center;gap:2px}
  .foot .dot{width:4px;height:4px;border-radius:50%;background:var(--red)}
  .url{position:absolute;right:24px;bottom:6px;font-size:2.8px;color:var(--light)}
  .brand{color:var(--red);display:flex;align-items:center;gap:4px}
  .brand .dot{border-radius:50%;background:var(--navy)}
  .icon{position:absolute}
  .just{text-align:justify}
</style>
</head>
<body>

<!-- 1 Cover -->
<section class="slide" style="left:93px;top:40px;background:linear-gradient(180deg,#1a8fd2,#1279c0)">
  <div class="photo" role="img" aria-label="Faint blue data wave background" style="inset:0;background:linear-gradient(90deg,rgba(255,255,255,.06),rgba(0,60,140,.15),rgba(255,255,255,.05))"></div>
  <div class="abs brand" style="left:0;right:0;top:36px;justify-content:center;font-size:17px"><span class="dot" style="width:14px;height:14px"></span>Ledger Lanternfox</div>
  <div class="abs white" style="left:0;right:0;top:89px;text-align:center;font-size:9.4px;line-height:1.2">Your title Presentation<br>Title Template goes here</div>
  <div class="abs para white" style="left:52px;right:52px;top:125px;text-align:center">A short welcome for the room that names the talk, the speaker and the main idea. Keep it to two or three calm lines so every seat can read it at once.</div>
  <div class="url" style="color:rgba(255,255,255,.35)">ledgerlanternfox.example</div>
</section>

<!-- 2 Contents -->
<section class="slide" style="left:433px;top:40px">
  <div class="abs" style="left:14px;top:17px"><div class="title" style="font-size:14px">Contents</div><div class="sub">Great Subtitle Here</div></div>
  <div class="abs" style="left:0;top:44px;width:22px;height:2px;background:var(--red)"></div>
  <div class="abs" style="left:22px;top:44px;width:12px;height:2px;background:var(--navy)"></div>
  <div class="photo" role="img" aria-label="Photo of a person working at a computer with code on screen" style="left:0;top:47px;width:130px;height:95px;background:linear-gradient(135deg,#3a3d44,#17191d 55%,#5b5d62)"></div>
  <div class="abs" style="left:150px;top:20px;width:108px">
    <div style="display:flex;gap:6px;margin-bottom:9px"><span style="color:var(--red);font-size:4.4px">01</span><div><div style="font-size:5.2px">Cover Slides</div><div class="para sm">Open strong with a clear title, a short welcome and the name of the speaker.</div></div></div>
    <div style="display:flex;gap:6px;margin-bottom:9px"><span style="color:var(--red);font-size:4.4px">02</span><div><div style="font-size:5.2px">Business Slides</div><div class="para sm">Share the story, the services and the people you help with your data work.</div></div></div>
    <div style="display:flex;gap:6px;margin-bottom:9px"><span style="color:var(--red);font-size:4.4px">03</span><div><div style="font-size:5.2px">Infographics</div><div class="para sm">Turn key points into simple icons and blocks that the room can scan quickly.</div></div></div>
    <div style="display:flex;gap:6px"><span style="color:var(--red);font-size:4.4px">04</span><div><div style="font-size:5.2px">Data Slides</div><div class="para sm">Show the numbers with bold charts and short notes that explain each result.</div></div></div>
  </div>
  <div class="foot"><span class="dot"></span>Ledger Lanternfox</div><div class="url">ledgerlanternfox.example &nbsp; 2</div>
</section>

<!-- 3 About -->
<section class="slide" style="left:773px;top:40px">
  <div class="abs" style="left:0;top:30px;width:18px;height:2px;background:var(--red)"></div>
  <div class="abs" style="left:18px;top:30px;width:14px;height:2px;background:var(--navy)"></div>
  <div class="photo" role="img" aria-label="Photo of network cables in a server rack" style="left:0;top:32px;width:150px;height:94px;background:linear-gradient(135deg,#1b2c7a,#2b5fc4 40%,#1a7a5a 70%,#1d2a60)"></div>
  <div class="abs" style="left:166px;top:32px"><div class="title">About Us</div><div class="sub">Great Subtitle Here</div></div>
  <div class="abs para just" style="left:166px;top:60px;width:94px">Share who you are and what you build with data. Explain the problem you solve for teams, how you keep systems healthy and fast, and why the people behind the servers matter just as much as the queries they run each day. Talk about your path in tech, the lessons that shaped you and the care you bring to every project. Close with one clear line on how the room can reach you after the talk today.</div>
  <div class="foot"><span class="dot"></span>Ledger Lanternfox</div><div class="url">ledgerlanternfox.example &nbsp; 3</div>
</section>

<!-- 4 Title with three points -->
<section class="slide" style="left:93px;top:233px">
  <div class="abs" style="left:0;top:0;width:280px;height:87px;background:linear-gradient(90deg,#d92c2b,#e23a36)"></div>
  <div class="abs white" style="left:19px;top:27px"><div class="title white">Your title slide<br>will be here</div><div class="sub" style="margin-left:3px">Great Subtitle Here</div></div>
  <div class="abs white" style="left:185px;top:38px;font-size:9px">Ledger Lanternfox</div>
  <div class="abs" style="left:183px;top:87px;width:97px;height:59px;background:var(--navy)"></div>
  <svg class="icon" style="left:20px;top:95px" width="9" height="9" viewBox="0 0 10 10"><circle cx="5" cy="5" r="4.2" fill="none" stroke="var(--navy)" stroke-width=".7"/><path d="M1 5h8M5 1c-2 2.5-2 5.5 0 8M5 1c2 2.5 2 5.5 0 8" fill="none" stroke="var(--navy)" stroke-width=".6"/></svg>
  <div class="abs" style="left:37px;top:95px;width:57px"><div class="head" style="font-size:3.4px">Lorem Ipsum is simply dummy text of the printing</div><div class="para sm" style="margin-top:2px">Reach teams around the world with shared tools, clear data and a calm plan that keeps every system healthy.</div></div>
  <svg class="icon" style="left:100px;top:95px" width="9" height="9" viewBox="0 0 10 10"><circle cx="5" cy="4" r="3" fill="none" stroke="var(--navy)" stroke-width=".7"/><path d="M3.8 7.4h2.4M4 8.8h2" stroke="var(--navy)" stroke-width=".7"/></svg>
  <div class="abs" style="left:116px;top:95px;width:58px"><div class="head" style="font-size:3.4px">Lorem Ipsum is simply dummy text of the printing</div><div class="para sm" style="margin-top:2px">Bring fresh ideas to old problems and share what you learn so others can grow with you along the way.</div></div>
  <svg class="icon" style="left:188px;top:95px" width="9" height="9" viewBox="0 0 10 10"><path d="M1 3l4-2 4 2v5l-4 1.5L1 8z M1 3l4 2 4-2M5 5v4.5" fill="none" stroke="#fff" stroke-width=".6"/></svg>
  <div class="abs" style="left:204px;top:95px;width:66px"><div class="head white" style="font-size:3.4px">Lorem Ipsum is simply dummy text of the printing</div><div class="para sm white" style="margin-top:2px">Package each lesson into simple steps that any team can take home, test and use on the very next day of work.</div></div>
  <div class="foot"><span class="dot"></span>Ledger Lanternfox</div><div class="url" style="right:110px">ledgerlanternfox.example &nbsp; 4</div>
</section>

<!-- 5 Title with photo -->
<section class="slide" style="left:433px;top:233px">
  <div class="abs" style="left:22px;top:24px"><div class="title">Your title<br>slide will<br>be here</div><div class="sub">Great Subtitle Here</div></div>
  <div class="abs para just" style="left:22px;top:88px;width:78px">Use this space for a short story that supports the title. Explain why the topic matters, what the room will learn and how it links to the next slide. Keep each line short and plain so people at the very back can follow along without effort.</div>
  <div class="photo" role="img" aria-label="Photo of colourful code on a screen with a red tint" style="left:125px;top:0;width:155px;height:158px;background:linear-gradient(180deg,#1c2530,#2a3a48 50%,#d7342f 52%,#c92a28)"></div>
  <div class="foot"><span class="dot"></span>Ledger Lanternfox</div>
</section>

<!-- 6 Extended title -->
<section class="slide" style="left:773px;top:233px">
  <div class="abs" style="left:0;top:26px;width:140px;height:105px;background:linear-gradient(90deg,#dd3431,#e8504c)"></div>
  <div class="photo" role="img" aria-label="Photo of a sunset over the sea" style="left:140px;top:26px;width:140px;height:105px;background:linear-gradient(180deg,#6d7b93,#c98a72 45%,#e8a27a 60%,#8a8aa0)"></div>
  <div class="abs white" style="left:17px;top:42px;font-size:10.4px;line-height:1.15">You can place<br>here an extended<br>title for the slide</div>
  <div class="abs para sm white just" style="left:18px;top:86px;width:108px">Use this space for a short story that supports the title. Explain why the topic matters, what the room will learn and how it links to the next slide. Keep each line plain and easy to read from the back.</div>
  <div class="foot"><span class="dot"></span>Ledger Lanternfox</div><div class="url">ledgerlanternfox.example &nbsp; 6</div>
</section>

<!-- 7 Break section -->
<section class="slide" style="left:93px;top:426px">
  <div class="photo" role="img" aria-label="Photo of a laptop keyboard in the dark" style="inset:0;background:linear-gradient(135deg,#2c3140,#0f1219 60%,#24293a)"></div>
  <svg class="abs" style="left:0;top:0" width="280" height="158"><path d="M135 0 Q95 80 140 158 H280 V0 Z" fill="var(--sky)"/></svg>
  <div class="abs brand" style="left:162px;top:22px;font-size:5.5px"><span class="dot" style="width:5px;height:5px"></span>Ledger Lanternfox</div>
  <div class="abs white" style="left:160px;top:44px;font-size:18px;line-height:1.3">BREAK<br>SECTION<br>SLIDE</div>
  <div class="abs para white just" style="left:160px;top:120px;width:88px">Take a short pause here, stretch, refill your coffee and get ready for the next part of the talk.</div>
</section>

<!-- 8 Title with three bars -->
<section class="slide" style="left:433px;top:426px">
  <div class="abs" style="left:22px;top:14px"><div class="title">Your title<br>slide will<br>be here</div><div class="sub">Great Subtitle Here</div></div>
  <div class="abs para just" style="left:22px;top:82px;width:78px">Use this space for a short story that supports the title. Explain why the topic matters, what the room will learn and how it links to the next slide. Keep each line plain so the back rows can follow.</div>
  <div class="abs" style="left:115px;top:25px;width:153px;height:30px;background:var(--navy)"></div>
  <div class="abs" style="left:115px;top:58px;width:153px;height:30px;background:var(--red)"></div>
  <div class="abs" style="left:115px;top:92px;width:153px;height:30px;background:var(--sky)"></div>
  <svg class="icon" style="left:123px;top:33px" width="14" height="12" viewBox="0 0 14 12"><rect x="1" y="5" width="6" height="5" fill="none" stroke="#fff" stroke-width=".8"/><path d="M7 5c0-3 6-3 6 0" fill="none" stroke="#fff" stroke-width=".8"/></svg>
  <svg class="icon" style="left:123px;top:66px" width="14" height="12" viewBox="0 0 14 12"><path d="M3 8a3 3 0 0 1 1-6 4 4 0 0 1 7 1 2.5 2.5 0 0 1 0 5" fill="none" stroke="#fff" stroke-width=".8"/><path d="M7 5v6M5 9l2 2 2-2" fill="none" stroke="#fff" stroke-width=".8"/></svg>
  <svg class="icon" style="left:124px;top:100px" width="12" height="14" viewBox="0 0 12 14"><ellipse cx="6" cy="3" rx="5" ry="2" fill="#fff"/><path d="M1 3v8c0 2.6 10 2.6 10 0V3" fill="#fff"/><path d="M1 6c0 2.6 10 2.6 10 0M1 9c0 2.6 10 2.6 10 0" fill="none" stroke="var(--sky)" stroke-width=".6"/></svg>
  <div class="abs" style="left:146px;top:31px;width:115px"><div class="head white">Subtitle Here</div><div class="para sm white">Share one clear point here and keep it to two short lines for the room.</div></div>
  <div class="abs" style="left:146px;top:64px;width:115px"><div class="head white">Subtitle Here</div><div class="para sm white">Share one clear point here and keep it to two short lines for the room.</div></div>
  <div class="abs" style="left:146px;top:98px;width:115px"><div class="head white">Subtitle Here</div><div class="para sm white">Share one clear point here and keep it to two short lines for the room.</div></div>
  <div class="foot"><span class="dot"></span>Ledger Lanternfox</div><div class="url">ledgerlanternfox.example &nbsp; 8</div>
</section>

<!-- 9 Two column -->
<section class="slide" style="left:773px;top:426px">
  <div class="abs brand" style="left:19px;top:8px;font-size:4px;color:var(--navy)"><span class="dot" style="width:4px;height:4px;background:var(--red)"></span>Ledger Lanternfox</div>
  <div class="abs" style="left:22px;top:31px"><div class="title">Your title slide<br>will be here</div><div class="sub">Great Subtitle Here</div></div>
  <div class="abs para just" style="left:126px;top:30px;width:136px">Use this space for a short story that supports the title. Explain why the topic matters, what the room will learn and how it links to the next slide. Keep each line plain and short so people at the back of the room can read along with ease.</div>
  <div class="abs" style="left:19px;top:82px;width:245px;height:76px;background:var(--navy)"></div>
  <div class="photo" role="img" aria-label="Illustration of a glowing audio wave" style="left:30px;top:78px;width:83px;height:70px;border:1px solid #8aa6d6;background:linear-gradient(180deg,#1a2a8a,#6c80c8 50%,#e8ecf6)"></div>
  <div class="abs para white just" style="left:126px;top:100px;width:132px">Add the second column here with a clear point, a short example and one takeaway. Keep the words simple and the lines short so every seat in the room can follow the idea without strain.</div>
  <div class="url" style="color:rgba(255,255,255,.4)">ledgerlanternfox.example &nbsp; 9</div>
</section>

<!-- 10 Quote -->
<section class="slide" style="left:93px;top:620px">
  <div class="abs brand" style="left:19px;top:8px;font-size:4px;color:var(--navy)"><span class="dot" style="width:4px;height:4px;background:var(--red)"></span>Ledger Lanternfox</div>
  <div class="abs" style="left:22px;top:30px"><div class="title">Your title slide</div><div class="sub">Great Subtitle Here</div></div>
  <div class="photo" role="img" aria-label="Photo of a person coding at a desk" style="left:147px;top:0;width:133px;height:158px;background:linear-gradient(135deg,#5a5650,#2a2724 50%,#13151a)"></div>
  <div class="abs" style="left:0;top:62px;width:183px;height:48px;background:var(--navy)"></div>
  <div class="abs white" style="left:16px;top:64px;font-size:15px">&ldquo;</div>
  <div class="abs white" style="left:35px;top:70px;width:122px;font-size:3.2px;line-height:1.65">Good data work is quiet care for the people who depend on it. Build systems that let teams rest easy, and share what you learn so the next person has an easier day.</div>
  <svg class="icon" style="left:167px;top:80px" width="6" height="10" viewBox="0 0 6 10"><path d="M1 1l4 4-4 4" fill="none" stroke="#fff" stroke-width="1"/></svg>
  <svg class="icon" style="left:18px;top:117px" width="14" height="12" viewBox="0 0 14 12"><rect x="1" y="5" width="6" height="5" fill="none" stroke="var(--navy)" stroke-width=".8"/><path d="M7 5c0-3 6-3 6 0" fill="none" stroke="var(--navy)" stroke-width=".8"/></svg>
  <div class="abs" style="left:41px;top:115px;width:80px"><div class="head">Subtitle Here</div><div class="para sm">Share one clear point here and keep it to two short lines.</div></div>
  <div class="foot"><span class="dot"></span>Ledger Lanternfox</div><div class="url" style="color:rgba(255,255,255,.3)">ledgerlanternfox.example &nbsp; 10</div>
</section>

<!-- 11 Numbers -->
<section class="slide" style="left:433px;top:620px">
  <div class="abs" style="left:22px;top:25px"><div class="title">Your title<br>slide here</div><div class="sub">Great Subtitle Here</div></div>
  <div class="abs" style="left:87px;top:25px;width:.6px;height:33px;background:var(--light)"></div>
  <div class="abs para sm" style="left:91px;top:27px;width:66px">A short note that backs up the main title and tells the room what the numbers below show.</div>
  <div class="abs" style="left:30px;top:77px;font-size:3px;color:var(--grey)">Gender Classification</div>
  <div class="abs" style="left:22px;top:85px;width:129px;height:26px;background:var(--navy);padding:4px 6px 0 22px"><div style="font-size:4.8px;color:#fff">1500+</div><div class="para sm white">People joined the sessions this year and shared their stories.</div></div>
  <div class="abs" style="left:22px;top:116px;width:129px;height:26px;background:var(--red);padding:4px 6px 0 22px"><div style="font-size:4.8px;color:#fff">900+</div><div class="para sm white">Teams used the guides to build calmer, healthier routines.</div></div>
  <div class="photo" role="img" aria-label="Photo of a laptop with code on screen" style="left:163px;top:0;width:117px;height:158px;background:linear-gradient(160deg,#1d2531,#0c0f14 55%,#2b3345)"></div>
  <div class="foot"><span class="dot"></span>Ledger Lanternfox</div><div class="url" style="color:rgba(255,255,255,.3)">ledgerlanternfox.example &nbsp; 11</div>
</section>

<!-- 12 Stats band -->
<section class="slide" style="left:773px;top:620px">
  <div class="abs" style="left:22px;top:30px"><div class="title">Your title slide will be here</div><div class="sub">Great Subtitle Here</div></div>
  <div class="photo" role="img" aria-label="Photo of code with a red tint" style="left:0;top:59px;width:280px;height:66px;background:linear-gradient(90deg,#d62e2c,#e24440 50%,#d83230)"></div>
  <div class="abs" style="left:8px;top:74px;width:264px;display:flex;justify-content:space-between">
    <div style="width:61px;height:35px;border:1px solid #fff;color:#fff;text-align:center;padding-top:5px"><div style="font-size:9px">34.123</div><div style="font-size:3.4px;line-height:1.1">Lorem Ipsum is simply<br>dummy text</div></div>
    <div style="width:61px;height:35px;border:1px solid #fff;color:#fff;text-align:center;padding-top:5px"><div style="font-size:9px">7.700</div><div style="font-size:3.4px;line-height:1.1">Lorem Ipsum is simply<br>dummy text</div></div>
    <div style="width:61px;height:35px;border:1px solid #fff;color:#fff;text-align:center;padding-top:5px"><div style="font-size:9px">3.000</div><div style="font-size:3.4px;line-height:1.1">Lorem Ipsum is simply<br>dummy text</div></div>
    <div style="width:61px;height:35px;border:1px solid #fff;color:#fff;text-align:center;padding-top:5px"><div style="font-size:9px">3.000</div><div style="font-size:3.4px;line-height:1.1">Lorem Ipsum is simply<br>dummy text</div></div>
  </div>
  <div class="abs para sm" style="left:30px;top:129px;width:220px;text-align:center">Add a short line here that explains where these numbers come from and why they matter to the people in the room today.</div>
  <div class="foot"><span class="dot"></span>Ledger Lanternfox</div><div class="url">ledgerlanternfox.example &nbsp; 12</div>
</section>

<!-- 13 Four points -->
<section class="slide" style="left:93px;top:813px">
  <div class="abs brand" style="left:19px;top:8px;font-size:4px;color:var(--navy)"><span class="dot" style="width:4px;height:4px;background:var(--red)"></span>Ledger Lanternfox</div>
  <div class="abs" style="left:0;right:0;top:15px;text-align:center"><div class="title" style="font-size:14px">Your title slide will be here</div><div class="sub">Great Subtitle Here</div></div>
  <div class="abs para just" style="left:20px;top:43px;width:240px">Use this space for a short story that supports the title. Explain why the topic matters, what the room will learn and how it links to the next slide. Keep each line plain and short so people at the back of the room can read along with ease and stay with you.</div>
  <div class="photo" role="img" aria-label="Photo of code with a red tint" style="left:0;top:98px;width:280px;height:60px;background:linear-gradient(90deg,#d02b2a,#dd3a37 50%,#cf2c2a)"></div>
  <div class="abs" style="left:15px;top:76px;width:250px;display:flex;justify-content:space-between">
    <div style="width:55px;text-align:center"><div style="font-size:4.4px;color:#111">Subtitle Here</div><div style="width:15px;height:15px;border-radius:50%;background:#fff;border:1px solid var(--navy);margin:7px auto 3px"></div><div class="para sm white just">Share one clear point here and keep it short so the room can follow.</div></div>
    <div style="width:55px;text-align:center"><div style="font-size:4.4px;color:#111">Subtitle Here</div><div style="width:15px;height:15px;border-radius:50%;background:#fff;border:1px solid var(--navy);margin:7px auto 3px"></div><div class="para sm white just">Share one clear point here and keep it short so the room can follow.</div></div>
    <div style="width:55px;text-align:center"><div style="font-size:4.4px;color:#111">Subtitle Here</div><div style="width:15px;height:15px;border-radius:50%;background:#fff;border:1px solid var(--navy);margin:7px auto 3px"></div><div class="para sm white just">Share one clear point here and keep it short so the room can follow.</div></div>
    <div style="width:55px;text-align:center"><div style="font-size:4.4px;color:#111">Subtitle Here</div><div style="width:15px;height:15px;border-radius:50%;background:#fff;border:1px solid var(--navy);margin:7px auto 3px"></div><div class="para sm white just">Share one clear point here and keep it short so the room can follow.</div></div>
  </div>
</section>

<!-- 14 Red with description -->
<section class="slide" style="left:433px;top:813px;background:linear-gradient(90deg,#d42d2b,#e13b37)">
  <div class="abs" style="left:22px;top:26px"><div class="title white" style="font-size:14px">Your title slide will be here</div><div class="sub white">Great Subtitle Here</div></div>
  <div class="abs white" style="left:208px;top:32px;font-size:5px">Ledger Lanternfox</div>
  <svg class="icon" style="left:26px;top:66px" width="9" height="11" viewBox="0 0 9 11"><path d="M1 1h5l2 2v7H1z M3 5h4M3 7h4" fill="none" stroke="#fff" stroke-width=".7"/></svg>
  <div class="abs" style="left:46px;top:64px;width:52px"><div class="head white" style="font-size:4.4px">Certificated</div><div class="para sm white">Share one short point here in two or three lines.</div></div>
  <svg class="icon" style="left:110px;top:66px" width="11" height="11" viewBox="0 0 11 11"><path d="M3 1h5v3a2.5 2.5 0 0 1-5 0zM5.5 6.5v2.5M3.5 10h4M3 2H1c0 2 1 2.5 2 2.5M8 2h2c0 2-1 2.5-2 2.5" fill="none" stroke="#fff" stroke-width=".7"/></svg>
  <div class="abs" style="left:131px;top:64px;width:52px"><div class="head white" style="font-size:4.4px">Awards</div><div class="para sm white">Share one short point here in two or three lines.</div></div>
  <svg class="icon" style="left:188px;top:65px" width="12" height="12" viewBox="0 0 12 12"><path d="M6 1l1.5 3.3 3.5.4-2.6 2.4.7 3.5L6 8.8 2.9 10.6l.7-3.5L1 4.7l3.5-.4z" fill="none" stroke="#fff" stroke-width=".7"/></svg>
  <div class="abs" style="left:215px;top:64px;width:52px"><div class="head white" style="font-size:4.4px">Favorite</div><div class="para sm white">Share one short point here in two or three lines.</div></div>
  <div class="abs" style="left:13px;top:97px;width:251px;height:61px;background:var(--navy)"></div>
  <div class="abs" style="left:23px;top:103px;width:4px;height:27px;background:var(--red)"></div>
  <div class="abs" style="left:42px;top:104px;width:205px"><div style="font-size:4.6px;color:#fff">Description</div><div class="para white just" style="margin-top:2px">Use this space for a short story that supports the title. Explain why the topic matters, what the room will learn and how it links to the next slide. Keep each line plain and short so people at the back of the room can read along with ease.</div></div>
  <div class="url" style="color:rgba(255,255,255,.4)">ledgerlanternfox.example &nbsp; 14</div>
</section>

<!-- 15 Three cards -->
<section class="slide" style="left:773px;top:813px">
  <div class="abs" style="left:0;top:0;width:280px;height:95px;background:linear-gradient(90deg,#d32c2a,#e03a36)"></div>
  <div class="abs" style="left:0;right:0;top:17px;text-align:center"><div class="title white" style="font-size:13.5px">Your title slide will be here</div><div class="sub white">Great Subtitle Here</div></div>
  <div class="abs" style="left:14px;top:56px;width:83px;height:79px;background:var(--navy)"></div>
  <div class="abs" style="left:97px;top:48px;width:85px;height:92px;background:var(--red);box-shadow:0 1px 4px rgba(0,0,0,.25)"></div>
  <div class="abs" style="left:182px;top:56px;width:84px;height:79px;background:var(--sky)"></div>
  <div class="abs" style="left:38px;top:45px;width:36px;height:36px;border-radius:50%;background:var(--navy);border:1.4px solid #fff"></div>
  <svg class="icon" style="left:50px;top:55px" width="12" height="16" viewBox="0 0 12 16"><path d="M1 1h10M1 15h10M2 1c0 5 8 5 8 7s-8 2-8 7M10 1c0 5-8 5-8 7s8 2 8 7" fill="none" stroke="#fff" stroke-width="1"/></svg>
  <div class="abs" style="left:121px;top:38px;width:36px;height:36px;border-radius:50%;background:var(--red);border:1.4px solid #fff"></div>
  <svg class="icon" style="left:130px;top:47px" width="18" height="18" viewBox="0 0 18 18"><circle cx="9" cy="9" r="6" fill="none" stroke="#fff" stroke-width="1"/><circle cx="9" cy="9" r="3" fill="none" stroke="#fff" stroke-width="1"/><path d="M9 1v16M1 9h16" stroke="#fff" stroke-width=".6"/></svg>
  <div class="abs" style="left:206px;top:45px;width:36px;height:36px;border-radius:50%;background:var(--sky);border:1.4px solid #fff"></div>
  <svg class="icon" style="left:217px;top:55px" width="14" height="16" viewBox="0 0 14 16"><path d="M3 15v-4C1 9.5 1 7 1 6a6 6 0 0 1 12 0l1 3h-2v3h-3v3" fill="#fff"/></svg>
  <div class="abs" style="left:20px;top:88px;width:71px;text-align:center"><div style="font-size:3.8px;color:#fff">Description</div><div class="para sm white" style="margin-top:2px">Share one clear point here and keep it to a few short lines for the room.</div></div>
  <div class="abs" style="left:102px;top:78px;width:75px;text-align:center"><div style="font-size:3.8px;color:#fff">Description</div><div class="para sm white" style="margin-top:2px">Use this card for the main idea. Explain why it matters, what changes for the team and how people can start using it on the very next day.</div></div>
  <div class="abs" style="left:188px;top:88px;width:72px;text-align:center"><div style="font-size:3.8px;color:#fff">Description</div><div class="para sm white" style="margin-top:2px">Share one clear point here and keep it to a few short lines for the room.</div></div>
  <div class="foot"><span class="dot"></span>Ledger Lanternfox</div><div class="url">ledgerlanternfox.example &nbsp; 15</div>
</section>

<!-- 16 Chart -->
<section class="slide" style="left:93px;top:1006px">
  <div class="abs" style="left:0;top:23px;width:24px;height:2px;background:var(--red)"></div>
  <div class="abs" style="left:24px;top:23px;width:14px;height:2px;background:var(--navy)"></div>
  <div class="abs" style="left:0;top:25px;width:280px;height:66px;background:var(--sky)"></div>
  <div class="abs" style="left:22px;top:31px"><div class="title white" style="font-size:13.5px">Your title slide will be here</div><div class="sub white">Great Subtitle Here</div></div>
  <div class="abs white" style="left:218px;top:36px;font-size:5px">Ledger Lanternfox</div>
  <div class="abs" style="left:19px;top:64px;width:250px;display:flex;justify-content:space-between;color:#fff">
    <div style="display:flex;gap:5px;align-items:center;width:82px"><span style="font-size:11px">48<small style="font-size:4px">%</small></span><div><div style="font-size:2.4px">BUSINESS MODELS</div><div style="font-size:2.6px;line-height:1.4;margin-top:1px">Clear steps that help teams work with less stress.</div></div></div>
    <div style="display:flex;gap:5px;align-items:center;width:82px"><span style="font-size:11px">84<small style="font-size:4px">%</small></span><div><div style="font-size:2.4px">BUSINESS MODELS</div><div style="font-size:2.6px;line-height:1.4;margin-top:1px">Clear steps that help teams work with less stress.</div></div></div>
    <div style="display:flex;gap:5px;align-items:center;width:82px"><span style="font-size:11px">79<small style="font-size:4px">%</small></span><div><div style="font-size:2.4px">BUSINESS MODELS</div><div style="font-size:2.6px;line-height:1.4;margin-top:1px">Clear steps that help teams work with less stress.</div></div></div>
  </div>
  <svg class="abs" style="left:30px;top:98px" width="230" height="45" viewBox="0 0 230 45">
    <g font-size="2.2" fill="#777" font-family="Questrial, sans-serif" text-anchor="middle">
      <line x1="0" y1="38" x2="208" y2="38" stroke="#ccc" stroke-width=".4"/>
      <rect x="8" y="12" width="7" height="26" fill="var(--navy)"/><rect x="17" y="24" width="7" height="14" fill="var(--red)"/><rect x="26" y="26" width="7" height="12" fill="var(--light)"/>
      <text x="20" y="42">Category 1</text>
      <rect x="61" y="20" width="7" height="18" fill="var(--navy)"/><rect x="70" y="11" width="7" height="27" fill="var(--red)"/><rect x="79" y="26" width="7" height="12" fill="var(--light)"/>
      <text x="73" y="42">Category 2</text>
      <rect x="114" y="17" width="7" height="21" fill="var(--navy)"/><rect x="123" y="28" width="7" height="10" fill="var(--red)"/><rect x="132" y="22" width="7" height="16" fill="var(--light)"/>
      <text x="126" y="42">Category 3</text>
      <rect x="167" y="10" width="7" height="28" fill="var(--navy)"/><rect x="176" y="21" width="7" height="17" fill="var(--red)"/><rect x="185" y="6" width="7" height="32" fill="var(--light)"/>
      <text x="179" y="42">Category 4</text>
      <rect x="196" y="17" width="1.5" height="1.5" fill="var(--navy)"/><text x="202" y="18.5">Series 1</text>
      <rect x="207" y="17" width="1.5" height="1.5" fill="var(--red)"/><text x="213" y="18.5">Series 2</text>
      <rect x="218" y="17" width="1.5" height="1.5" fill="var(--light)"/><text x="224" y="18.5">Series 3</text>
    </g>
  </svg>
  <div class="foot"><span class="dot"></span>Ledger Lanternfox</div><div class="url">ledgerlanternfox.example &nbsp; 16</div>
</section>

<!-- 17 Q&A -->
<section class="slide" style="left:433px;top:1006px;background:var(--sky)">
  <div class="photo" role="img" aria-label="Photo of a laptop keyboard" style="left:0;top:118px;width:280px;height:40px;background:linear-gradient(90deg,#1a1e28,#3a4152 60%,#151820)"></div>
  <svg class="abs" style="left:0;top:0" width="280" height="158"><polygon points="0,0 280,0 280,78 0,120" fill="var(--sky)"/><polygon points="0,120 280,78 280,95 0,127" fill="var(--navy)"/><polygon points="0,126 217,126 207,133 0,133" fill="var(--red)"/></svg>
  <div class="abs brand" style="left:27px;top:27px;font-size:10px"><span class="dot" style="width:9px;height:9px"></span>Ledger Lanternfox</div>
  <div class="abs white" style="left:69px;top:58px;font-size:37px;letter-spacing:1px">Q&amp;A</div>
  <div class="url" style="color:rgba(255,255,255,.3)">ledgerlanternfox.example &nbsp; 17</div>
</section>

<!-- 18 Contact / Thanks -->
<section class="slide" style="left:773px;top:1006px;background:linear-gradient(160deg,#e84a45,#d42d2b 55%,#e04440)">
  <div class="photo" role="img" aria-label="Photo of a sunset sky with a red tint" style="inset:0;background:linear-gradient(180deg,rgba(255,255,255,.08),rgba(0,0,0,.05) 60%,rgba(255,255,255,.06))"></div>
  <svg class="abs" style="left:0;top:0" width="280" height="158"><path d="M0 27 H120 Q140 78 125 130 H0 Z" fill="var(--navy)"/></svg>
  <div class="abs white" style="left:25px;top:37px;font-size:14px;line-height:1.15">Contact<br>Information</div>
  <div class="abs" style="left:27px;top:82px;font-size:3.4px;color:#fff;line-height:3.3">
    <div style="display:flex;align-items:center;gap:4px"><span style="width:5px;height:5px;background:#fff"></span>Your Account</div>
    <div style="display:flex;align-items:center;gap:4px"><span style="width:5px;height:5px;border-radius:50%;background:#fff"></span>@youraccount</div>
    <div style="display:flex;align-items:center;gap:4px"><svg width="5" height="4" viewBox="0 0 5 4"><rect x=".3" y=".3" width="4.4" height="3.4" fill="none" stroke="#fff" stroke-width=".5"/><path d="M.3.3l2.2 1.8L4.7.3" fill="none" stroke="#fff" stroke-width=".5"/></svg>your@account.com</div>
    <div style="display:flex;align-items:center;gap:4px"><span style="width:5px;height:5px;border-radius:50%;background:#fff"></span>your@account.com</div>
  </div>
  <div class="abs white" style="left:162px;top:72px;font-size:18px;letter-spacing:.2px">Thanks</div>
  <div class="abs" style="left:172px;top:91px;font-size:5.5px;color:#fff">For Your watching</div>
  <div class="url" style="color:rgba(255,255,255,.35)">ledgerlanternfox.example &nbsp; 18</div>
</section>

</body>
</html>
```